Landing page design for my current website

I need a landing page designed for my Wordpress website. My website is Velmorquay.com, and I need a page that will serve as a landing page for online ads I run. Please follow the color scheme of the current website

This web page will be targeted towards real estate owners who are looking for a property manager. Above the fold needs to have a CTA form headlined with "As a Rental Property Owner, I Want More Protection, Less Stress, and Drama-Free Living"

A few highlights that can be listed beyond the CTA and fold

- Comprehensive Property Management
Full-service management covering tenant placement, leasing, maintenance, and inspections.

Maximized Rental Income
Proven strategies to optimize rental rates and minimize vacancies, ensuring higher ROI.

Stress-Free Management
We handle all tenant interactions, maintenance requests, and property issues, so you don't have to.

Experienced Team
Over a decade of experience in managing single-family homes, small multifamily units, and apartment complexes.

Advanced Technology
Utilize cutting-edge property management software for efficient communication, rent collection, and maintenance tracking.

Tenant Screening and Placement
Thorough background checks and tenant screening processes to ensure reliable and responsible tenants.

Regular Property Inspections
Routine inspections to maintain property condition and address issues before they become costly problems.

Legal Compliance
Expertise in local and federal rental laws to keep your properties compliant and avoid legal hassles.

Transparent Reporting
Detailed monthly reports and financial statements to keep you informed about your property's performance.

Personalized Service
Tailored management plans to meet the unique needs of your properties and investment goals.
Effective Tenant Conflict Resolution
Skilled in handling challenging tenant situations, ensuring conflicts are resolved quickly and professionally to maintain a peaceful living environment and protect your investment.

```html
<!DOCTYPE html>
<html lang="en">
<head>
<meta charset="utf-8">
<title>Velmorquay Realty – Property Management for Rental Owners</title>
<link href="https://fonts.googleapis.com/css2?family=Poppins:wght@400;500;600;700;800&family=DM+Sans:wght@400;500&display=swap" rel="stylesheet">
<style>
:root{
  --brand-blue:#11427c;
  --ink:#1d1d1f;
  --dark:#333333;
  --icon-dark:#2f2f31;
  --muted:#444;
  --field:#f4f4f4;
  --white:#ffffff;
  --rule:#e6e6e6;
}
*{box-sizing:border-box;margin:0;padding:0}
html,body{width:734px;height:1200px;overflow:hidden;background:var(--white)}
body{position:relative;font-family:'Poppins',sans-serif;color:var(--ink)}

/* header */
.site-header{position:absolute;left:0;top:0;width:734px;height:41px;background:var(--white)}
.brand{position:absolute;left:68px;top:8px;display:flex;align-items:center;gap:6px}
.brand-dot{width:25px;height:25px;border-radius:50%;border:2px solid var(--brand-blue)}
.brand-name{font-weight:600;font-size:13px;color:var(--brand-blue);letter-spacing:.5px;text-transform:uppercase}
.header-phone{position:absolute;left:417px;top:14px;display:flex;align-items:center;gap:8px;font-size:8.5px;color:var(--ink)}
.header-phone svg{width:13px;height:13px}
.estimate-btn{position:absolute;left:516px;top:0;width:113px;height:41px;background:var(--brand-blue);color:var(--white);font-size:8px;font-weight:700;display:flex;align-items:center;justify-content:center;letter-spacing:.2px}
.menu-toggle{position:absolute;left:649px;top:15px;width:15px;height:12px;display:flex;flex-direction:column;justify-content:space-between}
.menu-toggle span{height:2px;background:var(--ink);border-radius:1px}

/* hero */
.hero{position:absolute;left:0;top:41px;width:734px;height:390px}
.hero-photo{position:absolute;inset:0;background:
  linear-gradient(180deg,rgba(40,52,48,.15) 0%,rgba(0,0,0,0) 40%,rgba(30,30,35,.2) 100%),
  linear-gradient(100deg,#3e4d44 0%,#2a3e63 30%,#24365c 55%,#515a60 80%,#6a7166 100%)}
.hero-photo::after{content:"";position:absolute;left:0;right:0;bottom:0;height:40px;background:linear-gradient(90deg,#8a1e22 0%,#6b6a66 30%,#8a8c8e 60%,#8a1e22 100%);opacity:.7}
.hero-welcome{position:absolute;left:69px;top:142px;font-size:15px;font-weight:700;color:var(--white)}
.hero-title{position:absolute;left:69px;top:172px;font-size:33px;font-weight:800;color:var(--white);letter-spacing:-.3px;text-transform:uppercase}
.hero-tagline{position:absolute;left:69px;top:217px;font-size:16px;font-weight:500;color:var(--white)}
.hero-cta{position:absolute;left:68px;top:255px;width:106px;height:36px;background:var(--white);color:var(--ink);font-size:8px;font-weight:700;display:flex;align-items:center;justify-content:center}

.lead-form{position:absolute;left:450px;top:32px;width:268px;height:338px;background:rgba(255,255,255,.94)}
.lead-form h2{position:absolute;left:15px;top:18px;width:250px;font-size:14px;font-weight:600;line-height:20.5px;color:var(--ink)}
.lead-form h2 em{font-style:normal;color:var(--brand-blue)}
.field{position:absolute;height:30px;background:var(--field);box-shadow:0 1px 3px rgba(0,0,0,.12);font-size:8.5px;color:#555;display:flex;align-items:center;padding-left:17px}
.field svg{position:absolute;right:14px;top:11px;width:10px;height:7px}
.policy-note{position:absolute;left:24px;top:251px;font-size:8.5px;color:#555}
.policy-note a{color:var(--brand-blue);text-decoration:underline}
.submit-btn{position:absolute;left:16px;top:285px;width:238px;height:30px;background:var(--brand-blue);color:var(--white);font-size:8.5px;font-weight:600;display:flex;align-items:center;justify-content:center}

/* features */
.features-title{position:absolute;left:0;top:481px;width:734px;text-align:center;font-size:25px;font-weight:800;color:#111}
.features-title span{color:var(--brand-blue)}
.features-rule{position:absolute;left:299px;top:522px;width:122px;height:3px;background:var(--rule)}
.features-wheel{position:absolute;left:0;top:0;width:734px;height:1030px}
.hub{position:absolute;left:284px;top:633px;width:168px;height:168px;border-radius:50%;background:var(--white);box-shadow:0 4px 14px rgba(0,0,0,.12);display:flex;align-items:center;justify-content:center;font-size:16px;font-weight:700;color:var(--brand-blue)}
.node{position:absolute;width:47px;height:47px;border-radius:50%;margin:-23.5px 0 0 -23.5px}
.node::after{content:"";position:absolute;inset:14px;border:2px solid rgba(255,255,255,.85);border-radius:50%}
.node.blue{background:var(--brand-blue)}
.node.dark{background:var(--icon-dark)}

.feature{position:absolute;font-size:8px;line-height:12.6px;color:var(--muted)}
.feature h3{font-size:9px;font-weight:500;color:#111;line-height:13px;margin-bottom:4px}
.feature.right-align{text-align:right}
.feature.center{text-align:center}

/* footer */
.site-footer{position:absolute;left:0;top:1027px;width:734px;height:173px;background:var(--dark);font-family:'DM Sans',sans-serif;color:var(--white)}
.footer-brand{position:absolute;left:67px;top:50px;display:flex;align-items:center;gap:7px}
.footer-brand .brand-dot{width:31px;height:31px;border-color:var(--white)}
.footer-brand .brand-name{font-family:'Poppins',sans-serif;font-size:16px;color:var(--white)}
.social{position:absolute;top:46px;width:20px;height:20px;border-radius:50%;background:var(--white)}
.contact{position:absolute;display:flex;gap:10px;font-size:9px;line-height:15.5px}
.contact svg{width:17px;height:17px;flex:none}
.footer-rule{position:absolute;left:67px;top:149px;width:598px;height:1px;background:#cfcfcf}
.copyright{position:absolute;left:67px;top:157px;font-size:7px}
.legal-links{position:absolute;right:69px;top:155px;font-size:7px;display:flex;gap:5px;align-items:center}
.legal-links i{width:1.5px;height:9px;background:var(--white)}
</style>
</head>
<body>

<header class="site-header">
  <div class="brand"><span class="brand-dot"></span><span class="brand-name">Velmorquay Realty</span></div>
  <div class="header-phone">
    <svg viewBox="0 0 24 24" fill="#11427c"><path d="M6.6 10.8a15 15 0 0 0 6.6 6.6l2.2-2.2c.3-.3.7-.4 1-.2 1.1.4 2.3.6 3.6.6.6 0 1 .4 1 1V20c0 .6-.4 1-1 1A17 17 0 0 1 3 4c0-.6.4-1 1-1h3.5c.6 0 1 .4 1 1 0 1.3.2 2.5.6 3.6.1.3 0 .7-.2 1z"/></svg>
    555.014.2290
  </div>
  <div class="estimate-btn">GET A FREE ESTIMATE</div>
  <div class="menu-toggle"><span></span><span></span><span></span></div>
</header>

<section class="hero">
  <div class="hero-photo" role="img" aria-label="Photo of a large navy-blue two-storey house with white gables, stone accents, trees behind and red flowers in front"></div>
  <p class="hero-welcome">Welcome To</p>
  <h1 class="hero-title">Velmorquay Realty</h1>
  <p class="hero-tagline">Excellence In Tenant Experience</p>
  <div class="hero-cta">GET STARTED</div>

  <form class="lead-form">
    <h2>As a <em>Rental Property Owner</em>, I Want More Protection, Less Stress, and Drama-Free Living</h2>
    <div class="field" style="left:15px;top:86px;width:239px">Full Name</div>
    <div class="field" style="left:16px;top:122px;width:238px">Email Address</div>
    <div class="field" style="left:17px;top:159px;width:112px">Phone Number</div>
    <div class="field" style="left:140px;top:159px;width:112px">Zip Code</div>
    <div class="field" style="left:16px;top:200px;width:238px">Interest
      <svg viewBox="0 0 10 7"><path d="M1 1l4 4 4-4" fill="none" stroke="#111" stroke-width="1.4"/></svg>
    </div>
    <p class="policy-note">Form submission agrees to <a>privacy policy</a></p>
    <div class="submit-btn">SUBMIT NOW</div>
  </form>
</section>

<h2 class="features-title">OUR <span>FEATURES</span></h2>
<div class="features-rule"></div>

<svg class="features-wheel" viewBox="0 0 734 1030" aria-hidden="true">
  <path d="M291 588 A148 148 0 1 0 455 594" fill="none" stroke="#2f2f31" stroke-width="2.2"/>
</svg>
<div class="hub">Velmorquay</div>

<span class="node blue" style="left:291px;top:588px"></span>
<span class="node dark" style="left:239px;top:645px"></span>
<span class="node blue" style="left:231px;top:726px"></span>
<span class="node dark" style="left:249px;top:797px"></span>
<span class="node blue" style="left:296px;top:844px"></span>
<span class="node dark" style="left:364px;top:864px"></span>
<span class="node blue" style="left:447px;top:845px"></span>
<span class="node dark" style="left:492px;top:794px"></span>
<span class="node blue" style="left:500px;top:729px"></span>
<span class="node dark" style="left:495px;top:657px"></span>
<span class="node blue" style="left:455px;top:594px"></span>

<div class="feature right-align" style="right:474px;top:550px;width:220px">
  <h3>Personalized Service</h3>
  <p style="margin-right:4px">Tailored management plans to meet the unique needs of your properties and investment goals.</p>
</div>
<div class="feature right-align" style="right:529px;top:618px;width:180px">
  <h3>Comprehensive Property<br>Management</h3>
  <p style="margin-right:4px">Full-service management covering tenant placement, leasing, maintenance, and inspections.</p>
</div>
<div class="feature right-align" style="right:537px;top:708px;width:190px">
  <h3>Maximized Rental Income</h3>
  <p>Proven strategies to optimize rental rates and minimize vacancies, ensuring higher ROI.</p>
</div>
<div class="feature right-align" style="right:521px;top:786px;width:180px">
  <h3>Stress-Free Management</h3>
  <p>We handle all tenant interactions, maintenance requests, and property issues, so you don't have to.</p>
</div>
<div class="feature right-align" style="right:463px;top:866px;width:175px">
  <h3>Experienced Team</h3>
  <p>Over a decade of experience in managing single-family homes, small multifamily units, and apartment complexes.</p>
</div>
<div class="feature center" style="left:287px;top:903px;width:150px">
  <h3>Advanced Technology</h3>
  <p>Utilize cutting-edge property management software for efficient communication, rent collection, and maintenance tracking.</p>
</div>
<div class="feature" style="left:468px;top:868px;width:180px">
  <h3>Tenant Screening and Placement</h3>
  <p>Thorough background checks and tenant screening processes to ensure reliable and responsible tenants.</p>
</div>
<div class="feature" style="left:528px;top:786px;width:180px">
  <h3>Regular Property Inspections</h3>
  <p>We handle all tenant interactions, maintenance requests, and property issues, so you don't have to.</p>
</div>
<div class="feature" style="left:534px;top:718px;width:195px">
  <h3>Legal Compliance</h3>
  <p style="margin-left:3px">Proven strategies to optimize rental rates and minimize vacancies, ensuring higher ROI.</p>
</div>
<div class="feature" style="left:531px;top:635px;width:190px">
  <h3 style="margin-bottom:7px">Transparent Reporting</h3>
  <p style="margin-left:2px">Detailed monthly reports and financial statements to keep you informed about your property's performance.</p>
</div>
<div class="feature" style="left:507px;top:557px;width:200px">
  <h3>Effective Tenant Conflict Resolution</h3>
  <p style="margin-left:2px">Skilled in handling challenging tenant situations, ensuring conflicts are resolved quickly and professionally to maintain a peaceful living environment and protect your investment.</p>
</div>

<footer class="site-footer">
  <div class="footer-brand"><span class="brand-dot"></span><span class="brand-name">Velmorquay Realty</span></div>
  <span class="social" style="left:561px"></span>
  <span class="social" style="left:587px"></span>
  <span class="social" style="left:611px"></span>
  <span class="social" style="left:638px"></span>

  <div class="contact" style="left:68px;top:98px">
    <svg viewBox="0 0 24 24"><circle cx="12" cy="12" r="12" fill="#fff"/><path d="M12 5a4.5 4.5 0 0 0-4.5 4.5c0 3.4 4.5 8.5 4.5 8.5s4.5-5.1 4.5-8.5A4.5 4.5 0 0 0 12 5zm0 6.2a1.7 1.7 0 1 1 0-3.4 1.7 1.7 0 0 1 0 3.4z" fill="#333"/></svg>
    <span>48 Alder Row,<br>Fernhollow PA, 17022</span>
  </div>
  <div class="contact" style="left:236px;top:106px">
    <svg viewBox="0 0 24 24"><circle cx="12" cy="12" r="12" fill="#fff"/><path d="M8.6 10.9a9 9 0 0 0 4.5 4.5l1.5-1.5c.2-.2.5-.3.7-.1.8.3 1.6.4 2.4.4.4 0 .7.3.7.7v2.4c0 .4-.3.7-.7.7A11.6 11.6 0 0 1 6 6.3c0-.4.3-.7.7-.7h2.4c.4 0 .7.3.7.7 0 .8.1 1.6.4 2.4.1.3 0 .5-.2.7z" fill="#333"/></svg>
    <span style="margin-left:2px">555.014.2290</span>
  </div>
  <div class="contact" style="left:368px;top:107px">
    <svg viewBox="0 0 24 24"><circle cx="12" cy="12" r="12" fill="#fff"/><rect x="6.5" y="8" width="11" height="8" rx="1" fill="#333"/><path d="M7 8.6l5 4 5-4" fill="none" stroke="#fff" stroke-width="1"/></svg>
    <span style="margin-left:2px">Hello@velmorquay.com</span>
  </div>

  <div class="footer-rule"></div>
  <p class="copyright">Copyright © 2024 velmorquay realty.All rights reserved.</p>
  <div class="legal-links"><span>Privacy Policy</span><i></i><span>Terms &amp; Conditions</span></div>
</footer>

</body>
</html>
```